website in progress for new building development

Hi,
I have a new real estate development website in making but am running out of time for its completion. It's for a new apartment building for sales. Would it be possible for you to change/alter the site according to my requirements? I could send you all the existing files. The bulk of the website is done.
The images aren't really ready yet but will be within the next days so those will need to be replaced. Currently draft images are the placeholder on the website.

Let me know if you would be interested so we can quickly pick up correspondence.

This is the website so far (using Wordpress):
http://lumerow.com.au/lumerow/

Our domain is:
lumerow.com.au

I am also adding the theme I am using.

Thanks.

Target Market(s)

Potential buyers.

Industry/Entity Type

Real Estate Development

Number of Pages Required

5+ page

Font styles to use
Other font styles liked:
• I used Robot under google fonts for the headlines

Requirements
Must have
• This is the current website
• http://lumerow.com.au/lumerow
• I'd like the colour scheme to remain the way it is.
• 1. Header
• I would like the header to have the menu on the right and have the 'Reigster' button similar to this website: (see the header here which shows up once you scroll down in the page) http://vantageofmeltonhaus.com.au/
• Please adjust this feature into our website with the menu items given.
• 2. Logo on Homepage
• Add the lumerow logo into the top center of the feature image.
• Though permanent images are yet to arrive in the next few days. These are only drafts.
• 3. Footer
• Not sure about the colour scheme here yet.
• Should contain Disclaimer and copyrights.
• 4.Pages:
• a) Home
• b) Building
• c) Interior
• d) Location
• e) Register
• 5. page 'Home'
• When you scroll down in lumerow.com.au/lumerow/ you see the three images under the feature image, I would like those being hyperlinked as a 'box' just like this website has them when you scroll down here:
• http://www.elmtoria.com.au/
• 6. page 'Register'
• I like the subtle colour scheme for the form used here http://vantageofmeltonhaus.com.au/#enquire-now
• and their 'Submit' button. Maybe adjust it to my website and remove the borders in the fields.
• 7. page 'Building'
• Will have two images of the exterior of the building which should be sliding automatically. (Images will be provided soon. For now I am only attaching draft images.)
• 8. page 'Interior'
• Will also have two images of the interior which should be automatically sliding. (Images will be provided soon. Attaching draft images for now)
Nice to have
• A language selection in the top right corner of each page:
• selection between english, mandarin, cantonese, korean.

```html
<!DOCTYPE html>
<html lang="en">
<head>
<meta charset="utf-8">
<title>Lumerow – Register Now</title>
<link rel="stylesheet" href="https://fonts.googleapis.com/css2?family=Roboto:wght@500;700&family=Open+Sans:wght@400;600;700&display=swap">
<style>
  :root {
    --ink-black: #000000;
    --page-bg: #ecebeb;
    --gold: #a8854d;
    --gold-light: #c9a266;
    --footer-bg: #333333;
    --label: #555555;
    --title: #3a3a3a;
    --field-bg: #ffffff;
    --field-line: #dcdcdc;
    --white: #ffffff;
  }
  * { box-sizing: border-box; margin: 0; padding: 0; }
  html, body { width: 1200px; height: 851px; overflow: hidden; }
  body {
    position: relative;
    background: var(--page-bg);
    font-family: "Open Sans", Arial, sans-serif;
    color: var(--label);
  }
  .site-header {
    position: absolute; left: 0; top: 0; width: 1200px; height: 107px;
    background: var(--ink-black);
  }
  .brand {
    position: absolute; left: 99px; top: 30px;
    display: flex; align-items: center; gap: 8px;
  }
  .brand-mark { width: 12px; height: 12px; background: var(--gold); }
  .brand-name {
    font-family: "Roboto", Arial, sans-serif; font-weight: 500;
    font-size: 18px; letter-spacing: 6px; color: var(--gold-light);
  }
  .main-nav {
    position: absolute; left: 479px; top: 45px;
    display: flex; gap: 31px;
    font-family: "Roboto", Arial, sans-serif; font-weight: 700;
    font-size: 14.5px; letter-spacing: 1.3px; color: var(--white);
  }
  .register-btn {
    position: absolute; left: 890px; top: 35px; width: 126px; height: 40px;
    background: var(--gold); color: var(--white);
    font-family: "Roboto", Arial, sans-serif; font-weight: 700;
    font-size: 14.5px; letter-spacing: 1.3px;
    display: flex; align-items: center; justify-content: center;
  }
  .lang-select {
    position: absolute; left: 1034px; top: 35px; width: 68px; height: 39px;
    border: 1px solid #bbbbbb; border-radius: 3px;
  }
  .lang-flag { position: absolute; left: 10px; top: 12px; width: 25px; height: 15px; background: #2b3f8c; }
  .lang-caret { position: absolute; left: 52px; top: 18px; }

  .page-title {
    position: absolute; left: 0; top: 162px; width: 1200px; text-align: center;
    font-family: "Roboto", Arial, sans-serif; font-weight: 700;
    font-size: 29px; letter-spacing: 2.6px; color: var(--title);
  }
  .label {
    position: absolute; left: 96px; font-size: 12px; color: var(--label);
    text-transform: uppercase;
  }
  .radio {
    position: absolute; top: 282px; width: 19px; height: 19px; border-radius: 50%;
    background: radial-gradient(circle, #f4f4f4 45%, #d3d3d3 100%);
  }
  .radio-label { position: absolute; top: 284px; font-size: 12px; }
  .field {
    position: absolute; height: 35px; background: var(--field-bg);
    border: 1px solid var(--field-line);
  }
  .select-arrow {
    position: absolute; right: 0; top: 0; width: 33px; height: 33px;
    background: #f0f0f0; border-left: 1px solid var(--field-line);
    display: flex; align-items: center; justify-content: center;
  }
  .submit-btn {
    position: absolute; left: 98px; top: 648px; width: 98px; height: 38px;
    background: var(--gold); color: var(--white);
    font-weight: 700; font-size: 14.5px;
    display: flex; align-items: center; justify-content: center;
  }
  .site-footer {
    position: absolute; left: 0; top: 752px; width: 1200px; height: 99px;
    background: var(--footer-bg);
    display: flex; align-items: center; justify-content: center;
    color: var(--white); font-size: 12.5px;
  }
  .site-footer .sep { margin: 0 9px; }
</style>
</head>
<body>
  <header class="site-header">
    <div class="brand"><span class="brand-mark"></span><span class="brand-name">LUMEROW</span></div>
    <nav class="main-nav"><span>HOME</span><span>BUILDING</span><span>INTERIOR</span><span>LOCATION</span></nav>
    <div class="register-btn">REGISTER</div>
    <div class="lang-select">
      <div class="lang-flag" role="img" aria-label="English language flag"></div>
      <svg class="lang-caret" width="10" height="6" viewBox="0 0 10 6"><path d="M0 0h10L5 6z" fill="#ffffff"/></svg>
    </div>
  </header>

  <h1 class="page-title">REGISTER NOW</h1>

  <div class="label" style="top:240px">Please select :</div>
  <span class="radio" style="left:98px"></span><span class="radio-label" style="left:135px">COMMERCIAL</span>
  <span class="radio" style="left:235px"></span><span class="radio-label" style="left:272px">RESIDENTIAL</span>
  <span class="radio" style="left:369px"></span><span class="radio-label" style="left:406px">RETAIL</span>

  <div class="label" style="top:334px">First name :</div>
  <div class="label" style="top:334px; left:618px">Last name :</div>
  <div class="field" style="left:97px; top:362px; width:484px"></div>
  <div class="field" style="left:618px; top:362px; width:484px"></div>

  <div class="label" style="top:413px">Email :</div>
  <div class="field" style="left:97px; top:435px; width:1005px"></div>

  <div class="label" style="top:487px">Phone number :</div>
  <div class="field" style="left:97px; top:509px; width:1005px"></div>

  <div class="label" style="top:562px">What language would you prefer to be contacted in ?</div>
  <div class="field" style="left:97px; top:585px; width:1005px">
    <div class="select-arrow"><svg width="10" height="6" viewBox="0 0 10 6"><path d="M0 0h10L5 6z" fill="#888888"/></svg></div>
  </div>

  <div class="submit-btn">SUBMIT</div>

  <footer class="site-footer">
    <span>Copyright © 2015 Lumerow. All rights reserved</span><span class="sep">|</span><span>Disclaimer</span>
  </footer>
</body>
</html>
```